Business Card Design Project

We are not a new company, but renamed to "Vantorin Kitchens" last year. We specialize in modern high-end cabinetry imports. We would like to communicate a sense of quality and cutting edge technology. Ideally the design would incorporate our logo colors, silver, red and preferably a black, matte background. Though we are open to suggestions.
Logo is attached.
Edit: I have attached rough drafts of the previous cards, this way you will have all necessary content that needs to go on the cards.
Updates
Project Deadline Extended
Reason: We have received a lot of great designs, but due to the sheer number we couldn't respond to all. We will extend the deadline for another 7 days to finalize and provide feedback to designers.
Thank you for your hard work!
Industry/Entity Type
Business
Look and feel
Each slider illustrates characteristics of the customer's brand and the style your logo design should communicate.

```html
<!DOCTYPE html>
<html lang="en">
<head>
<meta charset="utf-8">
<title>Vantorin Kitchens — Business Card</title>
<link rel="stylesheet" href="https://fonts.googleapis.com/css2?family=Cinzel:wght@400;600&display=swap">
<style>
  :root {
    --backdrop: #7a4f30;
    --card-white: #ffffff;
    --card-shade: #e4e4e4;
    --ink-dark: #2e2a2c;
    --ink-grey: #8a8a8a;
    --brand-silver: #7c7c7c;
    --band-deep: #362c35;
    --band-soft: #5b4f59;
    --rule: #d6d6d6;
  }
  * { box-sizing: border-box; margin: 0; padding: 0; }
  html, body { width: 1200px; height: 750px; overflow: hidden; }
  body {
    background: var(--backdrop);
    font-family: "Cinzel", "Times New Roman", serif;
    position: relative;
  }
  .card {
    position: absolute;
    left: 297px;
    width: 606px;
    height: 306px;
    border-radius: 22px;
    overflow: hidden;
    background: linear-gradient(160deg, var(--card-white) 45%, var(--card-shade) 100%);
    box-shadow: 0 4px 14px rgba(0,0,0,0.35);
  }
  .card--front { top: 18px; }
  .card--back { top: 418px; background: var(--card-white); }

  .brand {
    position: absolute;
    inset: 0;
    display: flex;
    align-items: center;
    justify-content: center;
    gap: 16px;
    padding-bottom: 30px;
  }
  .brand__mark {
    width: 22px; height: 22px;
    background: var(--brand-silver);
  }
  .brand__name {
    font-size: 38px;
    font-weight: 600;
    color: var(--brand-silver);
    letter-spacing: 1px;
  }

  .accent-band {
    position: absolute;
    left: 0;
    right: 0;
    bottom: 0;
    height: 72px;
    background: linear-gradient(180deg, var(--band-deep), var(--band-soft));
  }

  .holder {
    position: absolute;
    right: 38px;
    top: 58px;
    width: 290px;
    text-align: right;
  }
  .holder__name {
    font-size: 22px;
    font-weight: 400;
    color: var(--ink-dark);
    letter-spacing: 2px;
  }
  .holder__title {
    font-size: 14px;
    color: var(--ink-grey);
    letter-spacing: 1px;
    margin-top: -2px;
  }
  .holder__rule {
    height: 2px;
    margin-top: 8px;
    background: linear-gradient(90deg, transparent, var(--rule) 30%, var(--rule) 85%, transparent);
  }

  .contacts {
    position: absolute;
    left: 250px;
    top: 137px;
    width: 95px;
    list-style: none;
    text-align: right;
    font-size: 14px;
    line-height: 16.5px;
    color: var(--ink-dark);
  }
</style>
</head>
<body>
  <section class="card card--front">
    <div class="brand">
      <span class="brand__mark"></span>
      <span class="brand__name">Vantorin Kitchens</span>
    </div>
  </section>

  <section class="card card--back">
    <div class="accent-band" role="img" aria-label="Decorative dark plum swoosh with a thin white line along the lower part of the card"></div>

    <div class="holder">
      <p class="holder__name">Marcus Delane</p>
      <p class="holder__title">Director</p>
      <div class="holder__rule"></div>
    </div>

    <ul class="contacts">
      <li>Address:</li>
      <li>Phone:</li>
      <li>Cell:</li>
      <li>Fax:</li>
      <li>Email:</li>
    </ul>
  </section>
</body>
</html>
```